Redesign 2016 Digital Marketing Website and Convert to Wordpress

Technology needed to integrate:

- redesign and convert to wordpress
- gravity forms
- malware and hacker defense / honeypot (must be very secure from hackers)
- I want gravity forms to be a flow that asks many questions with icons and progress bar.
- 1 home page design
- 1 blog design
- 1 design for internal page content
- 1 multi step gravity form
I want to focus on SMB's. We are a marketing agency thats been around since 2016.

Site is: tallpine.agency

I am looking to redesign the homepage, blog page and services page. The services page will be a template for all inner pages of the site. All content needs to be moved into the new design.

I want to get ride of the weird video.

I need you to install gravity forms pro model so we can pass utms.

I need the gravity form to be a multi step form with icons.

All "contact us" or "get a free assesments" call to actions will go to this form only.

step 1:
what is your website

step 2:
what industry are you in
- option
- Home Services
- Legal
- Ecommerce
- Lead Gen

No matter which one they select its going to produce a differnt calculator for them.

Law:
How many leads did you get last month
how much is each ase worth on average
How much revenue do you want to make

Home servicse:
How many bookings did you get last month
How much is each service worht on average
How much revenue do you wangt to make

Ecommerce:
What is your average order value
How muny purchases did you have last month
How much revenue did you drive
How much revenue do you want to drive

For lead gen:
How many leads did you get lawt month
How much revenue did they generate

Step 3:
What is your current advertising budget

step 4:
Do you have a CRM and if so what is it

Step 5:
What is your personal informagtion
name
email
phone

Let me know if this is enough to get you going

Small and medium sized law firms, ecommerce, home services and lead gen customers.

We are a digital marketing agency

• Use whats on the current site and improve upon it

• Must be very secure, developed into a wordpress website. using gravity forms. remove my photo and my staffs photo, depersonalize it so it doesnt mention me or sam crolley. Use the same color scheme. I am looking to redesign the homepage, blog page and services page. The services page will be a template for all inner pages of the site. All content needs to be moved into the new design. I want to get ride of the weird video. I need you to install gravity forms pro model so we can pass utms. I need the gravity form to be a multi step form with icons. All "contact us" or "get a free assesments" call to actions will go to this form only. step 1: what is your website step 2: what industry are you in - option - Home Services - Legal - Ecommerce - Lead Gen No matter which one they select its going to produce a differnt calculator for them. Law: How many leads did you get last month how much is each ase worth on average How much revenue do you want to make Home servicse: How many bookings did you get last month How much is each service worht on average How much revenue do you wangt to make Ecommerce: What is your average order value How muny purchases did you have last month How much revenue did you drive How much revenue do you want to drive For lead gen: How many leads did you get lawt month How much revenue did they generate How much revenue do you want to make Step 3: What is your current advertising budget step 4: Do you have a CRM and if so what is it Step 5: What is your personal informagtion name email phone Let me know if this is enough to get you going
• SHOULD NOT BE SLOPPY, I AM LOOKING FOR ATTENTION TO DETAIL.

```html
<!DOCTYPE html>
<html lang="en">
<head>
<meta charset="utf-8">
<title>Tall Pine – Free Assessment Flow</title>
<link rel="stylesheet" href="https://fonts.googleapis.com/css2?family=Poppins:wght@300;400;500;600;700;800&display=swap">
<style>
:root{
  --stage:#6e1216;
  --brand:#7a1317;
  --orange:#f7931e;
  --ink:#2a2a2a;
  --bar:#2b2b2b;
  --muted:#555;
  --line:#c4c4c4;
  --rule:#e8e8e8;
  --white:#fff;
}
*{box-sizing:border-box;margin:0;padding:0}
html,body{width:1200px;height:870px;overflow:hidden;background:var(--stage);font-family:'Poppins',sans-serif;color:var(--ink)}
.canvas{position:relative;width:1200px;height:870px}
.page{position:absolute;width:711px;background:var(--white);transform:scale(.5291);transform-origin:0 0}
.page--1{left:18px;top:16px}
.page--2{left:411px;top:16px}
.page--3{left:804px;top:16px}
.page--4{left:206px;top:438px}
.page--5{left:599px;top:438px}

.topbar{height:53px;display:flex;align-items:center;padding:0 44px;position:relative}
.brand{display:flex;align-items:center;gap:9px}
.brand__mark{width:35px;height:35px;border-radius:50%;background:var(--brand)}
.brand__name{font-size:15px;font-weight:400;letter-spacing:1.6px;color:var(--muted);line-height:1}
.brand__tag{font-size:5.5px;letter-spacing:2.6px;color:#777;margin-top:4px}
.callout{position:absolute;left:334px;top:20px;font-size:10.5px;font-weight:700;color:var(--ink)}
.callout b{color:var(--brand)}
.cta{position:absolute;left:534px;top:13px;width:133px;height:28px;background:var(--orange);color:var(--white);font-size:9.5px;font-weight:600;display:flex;align-items:center;justify-content:center;letter-spacing:.2px}
.nav{height:33px;background:var(--bar);display:flex;justify-content:center;align-items:center;gap:28px;font-size:8.5px;color:var(--white);letter-spacing:.3px}

.main{position:relative;height:305px;border-bottom:1px solid var(--rule)}
.page--1 .main{height:295px}
.title{position:absolute;top:34px;left:0;right:0;text-align:center;font-size:21px;font-weight:700;letter-spacing:.2px}
.title::after{content:"";display:block;width:70px;height:3px;background:var(--brand);margin:7px auto 0}
.stepper{position:absolute;top:95px;left:0;right:0;display:flex;justify-content:center;align-items:center}
.dot{width:33px;height:33px;border-radius:50%;border:2px solid var(--line);color:var(--line);display:flex;align-items:center;justify-content:center;font-size:13px;font-weight:600}
.dot.on{border-color:var(--brand);color:var(--brand)}
.link{width:56px;height:1.5px;background:var(--line)}
.link.on{background:var(--brand)}
.link.half{background:linear-gradient(90deg,var(--brand) 50%,var(--line) 50%)}
.step{position:absolute;left:173px;top:156px;width:400px}
.step__head{display:flex;align-items:center;gap:8px}
.step__icon{width:26px;height:26px;flex:none}
.step__num{font-size:11px;font-weight:700;color:var(--brand)}
.step__q{font-size:9.5px;margin-top:3px}
.row{display:flex;gap:6px;margin-top:14px}
.field{height:30px;border:1px solid #cfcfcf;font-size:7px;color:#333;display:flex;align-items:center;padding:0 11px;justify-content:space-between}
.field--wide{width:293px}
.next{width:68px;height:30px;background:var(--bar);color:var(--white);font-size:11px;font-weight:700;display:flex;align-items:center;justify-content:center;gap:6px}
.grid5{display:grid;grid-template-columns:141px 141px 76px;grid-template-rows:30px 30px;gap:6px 10px;margin-top:14px}
.grid5 .email{grid-column:1/3}
.submit{grid-column:3;grid-row:1/3;background:var(--orange);color:var(--white);font-size:11.5px;font-weight:700;display:flex;align-items:center;justify-content:center;gap:6px}

.badges{height:90px;border-bottom:1px solid var(--rule);position:relative;display:flex;align-items:center;padding:0 44px}
.partner{position:absolute;left:245px;top:20px;display:flex;gap:8px;align-items:stretch;height:50px}
.partner__strip{width:12px;background:#e33b2f}
.partner__plate{width:88px;background:#ececec;border-radius:4px}
.seal{position:absolute;left:406px;top:19px;width:52px;height:52px;border-radius:50%;background:#1f4d7a;border:3px solid #c9d6e3}
.follow{position:absolute;left:524px;top:22px}
.follow__label{font-size:10.5px;letter-spacing:.3px}
.socials{display:flex;gap:15px;margin-top:11px}
.socials span{width:15px;height:15px;border-radius:50%;background:var(--ink)}

.links{height:233px;border-bottom:1px solid var(--rule);position:relative}
.col{position:absolute;top:24px}
.col h3{font-size:14px;font-weight:700;letter-spacing:.2px;margin-bottom:9px}
.col li{list-style:none;font-size:7.3px;color:#444;line-height:1.55;margin-bottom:6px}
.col--quick{left:44px}.col--services{left:188px}.col--industries{left:364px}.col--guides{left:523px;width:150px}
.col--guides li{margin-bottom:9px}
.legal{height:48px;display:flex;align-items:center;justify-content:center;font-size:7.3px;color:#555;padding-right:70px}
</style>
</head>
<body>
<div class="canvas">

<!-- Page: step 1 -->
<section class="page page--1">
  <header class="topbar">
    <div class="brand"><span class="brand__mark"></span><div><div class="brand__name">TALL PINE</div><div class="brand__tag">GROWTH MARKETING</div></div></div>
    <div class="callout">OR CALL US NOW : <b>(480) 555-0142</b></div>
    <a class="cta">GROW YOUR REVENUE</a>
  </header>
  <nav class="nav"><span>HOME</span><span>ABOUT</span><span>INDUSTRIES</span><span>SERVICES</span><span>RESOURCES</span><span>TRAINING</span><span>BLOG</span><span>CONTACT US</span></nav>
  <main class="main">
    <h1 class="title">GET A FREE ASSESSMENTS</h1>
    <div class="stepper"><span class="dot on">1</span><span class="link half"></span><span class="dot">2</span><span class="link"></span><span class="dot">3</span><span class="link"></span><span class="dot">4</span><span class="link"></span><span class="dot">5</span></div>
    <div class="step">
      <div class="step__head">
        <svg class="step__icon" viewBox="0 0 26 26" fill="none" stroke="#7a1317" stroke-width="1.2"><circle cx="13" cy="13" r="11"/><ellipse cx="13" cy="13" rx="5" ry="11"/><path d="M2 13h22M4 7h18M4 19h18"/></svg>
        <div><div class="step__num">Step 1</div><div class="step__q">What is your website</div></div>
      </div>
      <div class="row"><div class="field field--wide">Enter business name</div><div class="next">NEXT <span>›</span></div></div>
    </div>
  </main>
  <div class="badges">
    <div class="brand"><span class="brand__mark"></span><div><div class="brand__name">TALL PINE</div><div class="brand__tag">GROWTH MARKETING</div></div></div>
    <div class="partner"><span class="partner__strip"></span><span class="partner__plate"></span></div>
    <span class="seal"></span>
    <div class="follow"><div class="follow__label">FOLLOW US</div><div class="socials"><span></span><span></span><span></span><span></span><span></span></div></div>
  </div>
  <div class="links">
    <ul class="col col--quick"><h3>QUICK LINKS</h3><li>About</li><li>Industries</li><li>Services</li><li>Resources</li><li>Training</li><li>Blog</li><li>Contact Us</li></ul>
    <ul class="col col--services"><h3>SERVICES</h3><li>Programmatic Advertising</li><li>Search Engine Marketing (SEM)</li><li>Search Engine Optimization (SEO)</li><li>Content Marketing</li><li>Email Marketing</li><li>Paid Search Advertising</li><li>Paid Social Advertising</li></ul>
    <ul class="col col--industries"><h3>INDUSTRIES</h3><li>Ecommerce</li><li>Electricians</li><li>Financial Services Marketing</li><li>Home Builders</li><li>Home Services</li><li>Hvac Companies</li><li>Cosmetic Surgery Centers</li><li>Dental Marketing</li></ul>
    <ul class="col col--guides"><h3>GUIDES</h3><li>Ultimate Guide On Growing Your Medical Practice Business</li><li>Legal Marketing Strategy Guide For Law Firm Offices</li><li>Ultimate Flashgram Ads Guide To Skyrocket Your Leads And Sales</li><li>Ultimate Guide To Search Engine Queries</li></ul>
  </div>
  <footer class="legal">Copyright © 2024 CompanyName&nbsp; All Rights Reserved. Privacy Policy, Terms Of Use, Press &amp; Media, Cookie Policy</footer>
</section>

<!-- Page: step 2 -->
<section class="page page--2">
  <header class="topbar">
    <div class="brand"><span class="brand__mark"></span><div><div class="brand__name">TALL PINE</div><div class="brand__tag">GROWTH MARKETING</div></div></div>
    <div class="callout">OR CALL US NOW : <b>(480) 555-0142</b></div>
    <a class="cta">GROW YOUR REVENUE</a>
  </header>
  <nav class="nav"><span>HOME</span><span>ABOUT</span><span>INDUSTRIES</span><span>SERVICES</span><span>RESOURCES</span><span>TRAINING</span><span>BLOG</span><span>CONTACT US</span></nav>
  <main class="main">
    <h1 class="title">GET A FREE ASSESSMENTS</h1>
    <div class="stepper"><span class="dot on">1</span><span class="link on"></span><span class="dot on">2</span><span class="link half"></span><span class="dot">3</span><span class="link"></span><span class="dot">4</span><span class="link"></span><span class="dot">5</span></div>
    <div class="step">
      <div class="step__head">
        <svg class="step__icon" viewBox="0 0 26 26" fill="none" stroke="#7a1317" stroke-width="1.2"><rect x="5" y="2" width="11" height="22"/><rect x="16" y="10" width="7" height="14"/><path d="M8 6h2M12 6h2M8 10h2M12 10h2M8 14h2M12 14h2M8 18h2M12 18h2M18 14h3M18 18h3M2 24h23"/></svg>
        <div><div class="step__num">Step 2</div><div class="step__q">What industry are you in</div></div>
      </div>
      <div class="row"><div class="field field--wide">Select Option <span>⇕</span></div><div class="next">NEXT <span>›</span></div></div>
    </div>
  </main>
  <div class="badges">
    <div class="brand"><span class="brand__mark"></span><div><div class="brand__name">TALL PINE</div><div class="brand__tag">GROWTH MARKETING</div></div></div>
    <div class="partner"><span class="partner__strip"></span><span class="partner__plate"></span></div>
    <span class="seal"></span>
    <div class="follow"><div class="follow__label">FOLLOW US</div><div class="socials"><span></span><span></span><span></span><span></span><span></span></div></div>
  </div>
  <div class="links">
    <ul class="col col--quick"><h3>QUICK LINKS</h3><li>About</li><li>Industries</li><li>Services</li><li>Resources</li><li>Training</li><li>Blog</li><li>Contact Us</li></ul>
    <ul class="col col--services"><h3>SERVICES</h3><li>Programmatic Advertising</li><li>Search Engine Marketing (SEM)</li><li>Search Engine Optimization (SEO)</li><li>Content Marketing</li><li>Email Marketing</li><li>Paid Search Advertising</li><li>Paid Social Advertising</li></ul>
    <ul class="col col--industries"><h3>INDUSTRIES</h3><li>Ecommerce</li><li>Electricians</li><li>Financial Services Marketing</li><li>Home Builders</li><li>Home Services</li><li>Hvac Companies</li><li>Cosmetic Surgery Centers</li><li>Dental Marketing</li></ul>
    <ul class="col col--guides"><h3>GUIDES</h3><li>Ultimate Guide On Growing Your Medical Practice Business</li><li>Legal Marketing Strategy Guide For Law Firm Offices</li><li>Ultimate Flashgram Ads Guide To Skyrocket Your Leads And Sales</li><li>Ultimate Guide To Search Engine Queries</li></ul>
  </div>
  <footer class="legal">Copyright © 2024 CompanyName&nbsp; All Rights Reserved. Privacy Policy, Terms Of Use, Press &amp; Media, Cookie Policy</footer>
</section>

<!-- Page: step 3 -->
<section class="page page--3">
  <header class="topbar">
    <div class="brand"><span class="brand__mark"></span><div><div class="brand__name">TALL PINE</div><div class="brand__tag">GROWTH MARKETING</div></div></div>
    <div class="callout">OR CALL US NOW : <b>(480) 555-0142</b></div>
    <a class="cta">GROW YOUR REVENUE</a>
  </header>
  <nav class="nav"><span>HOME</span><span>ABOUT</span><span>INDUSTRIES</span><span>SERVICES</span><span>RESOURCES</span><span>TRAINING</span><span>BLOG</span><span>CONTACT US</span></nav>
  <main class="main">
    <h1 class="title">GET A FREE ASSESSMENTS</h1>
    <div class="stepper"><span class="dot on">1</span><span class="link on"></span><span class="dot on">2</span><span class="link on"></span><span class="dot on">3</span><span class="link half"></span><span class="dot">4</span><span class="link"></span><span class="dot">5</span></div>
    <div class="step">
      <div class="step__head">
        <svg class="step__icon" viewBox="0 0 26 26" fill="none" stroke="#7a1317" stroke-width="1.2"><rect x="9" y="2" width="14" height="22" rx="1"/><rect x="11" y="4" width="10" height="5"/><path d="M12 12h2M16 12h2M20 12h1M12 16h2M16 16h2M12 20h2M16 20h2"/><circle cx="6" cy="19" r="4.5"/><path d="M6 16.5v5M4.5 18h2.5"/></svg>
        <div><div class="step__num">Step 3</div><div class="step__q">What is your current advertising budget</div></div>
      </div>
      <div class="row"><div class="field field--wide">Enter budget</div><div class="next">NEXT <span>›</span></div></div>
    </div>
  </main>
  <div class="badges">
    <div class="brand"><span class="brand__mark"></span><div><div class="brand__name">TALL PINE</div><div class="brand__tag">GROWTH MARKETING</div></div></div>
    <div class="partner"><span class="partner__strip"></span><span class="partner__plate"></span></div>
    <span class="seal"></span>
    <div class="follow"><div class="follow__label">FOLLOW US</div><div class="socials"><span></span><span></span><span></span><span></span><span></span></div></div>
  </div>
  <div class="links">
    <ul class="col col--quick"><h3>QUICK LINKS</h3><li>About</li><li>Industries</li><li>Services</li><li>Resources</li><li>Training</li><li>Blog</li><li>Contact Us</li></ul>
    <ul class="col col--services"><h3>SERVICES</h3><li>Programmatic Advertising</li><li>Search Engine Marketing (SEM)</li><li>Search Engine Optimization (SEO)</li><li>Content Marketing</li><li>Email Marketing</li><li>Paid Search Advertising</li><li>Paid Social Advertising</li></ul>
    <ul class="col col--industries"><h3>INDUSTRIES</h3><li>Ecommerce</li><li>Electricians</li><li>Financial Services Marketing</li><li>Home Builders</li><li>Home Services</li><li>Hvac Companies</li><li>Cosmetic Surgery Centers</li><li>Dental Marketing</li></ul>
    <ul class="col col--guides"><h3>GUIDES</h3><li>Ultimate Guide On Growing Your Medical Practice Business</li><li>Legal Marketing Strategy Guide For Law Firm Offices</li><li>Ultimate Flashgram Ads Guide To Skyrocket Your Leads And Sales</li><li>Ultimate Guide To Search Engine Queries</li></ul>
  </div>
  <footer class="legal">Copyright © 2024 CompanyName&nbsp; All Rights Reserved. Privacy Policy, Terms Of Use, Press &amp; Media, Cookie Policy</footer>
</section>

<!-- Page: step 4 -->
<section class="page page--4">
  <header class="topbar">
    <div class="brand"><span class="brand__mark"></span><div><div class="brand__name">TALL PINE</div><div class="brand__tag">GROWTH MARKETING</div></div></div>
    <div class="callout">OR CALL US NOW : <b>(480) 555-0142</b></div>
    <a class="cta">GROW YOUR REVENUE</a>
  </header>
  <nav class="nav"><span>HOME</span><span>ABOUT</span><span>INDUSTRIES</span><span>SERVICES</span><span>RESOURCES</span><span>TRAINING</span><span>BLOG</span><span>CONTACT US</span></nav>
  <main class="main">
    <h1 class="title">GET A FREE ASSESSMENTS</h1>
    <div class="stepper"><span class="dot on">1</span><span class="link on"></span><span class="dot on">2</span><span class="link on"></span><span class="dot on">3</span><span class="link on"></span><span class="dot on">4</span><span class="link half"></span><span class="dot">5</span></div>
    <div class="step">
      <div class="step__head">
        <svg class="step__icon" viewBox="0 0 26 26" fill="none" stroke="#7a1317" stroke-width="1.2"><circle cx="13" cy="13" r="4"/><circle cx="13" cy="4" r="2.5"/><circle cx="4" cy="20" r="2.5"/><circle cx="22" cy="20" r="2.5"/><path d="M13 6.5V9M6 18.5l3.6-2.6M20 18.5l-3.6-2.6M2 25c0-2 1-3 2-3s2 1 2 3M20 25c0-2 1-3 2-3s2 1 2 3"/></svg>
        <div><div class="step__num">Step 4</div><div class="step__q">Do you have a CRM and if so what is it</div></div>
      </div>
      <div class="row"><div class="field field--wide">Enter CRM details</div><div class="next">NEXT <span>›</span></div></div>
    </div>
  </main>
  <div class="badges">
    <div class="brand"><span class="brand__mark"></span><div><div class="brand__name">TALL PINE</div><div class="brand__tag">GROWTH MARKETING</div></div></div>
    <div class="partner"><span class="partner__strip"></span><span class="partner__plate"></span></div>
    <span class="seal"></span>
    <div class="follow"><div class="follow__label">FOLLOW US</div><div class="socials"><span></span><span></span><span></span><span></span><span></span></div></div>
  </div>
  <div class="links">
    <ul class="col col--quick"><h3>QUICK LINKS</h3><li>About</li><li>Industries</li><li>Services</li><li>Resources</li><li>Training</li><li>Blog</li><li>Contact Us</li></ul>
    <ul class="col col--services"><h3>SERVICES</h3><li>Programmatic Advertising</li><li>Search Engine Marketing (SEM)</li><li>Search Engine Optimization (SEO)</li><li>Content Marketing</li><li>Email Marketing</li><li>Paid Search Advertising</li><li>Paid Social Advertising</li></ul>
    <ul class="col col--industries"><h3>INDUSTRIES</h3><li>Ecommerce</li><li>Electricians</li><li>Financial Services Marketing</li><li>Home Builders</li><li>Home Services</li><li>Hvac Companies</li><li>Cosmetic Surgery Centers</li><li>Dental Marketing</li></ul>
    <ul class="col col--guides"><h3>GUIDES</h3><li>Ultimate Guide On Growing Your Medical Practice Business</li><li>Legal Marketing Strategy Guide For Law Firm Offices</li><li>Ultimate Flashgram Ads Guide To Skyrocket Your Leads And Sales</li><li>Ultimate Guide To Search Engine Queries</li></ul>
  </div>
  <footer class="legal">Copyright © 2024 CompanyName&nbsp; All Rights Reserved. Privacy Policy, Terms Of Use, Press &amp; Media, Cookie Policy</footer>
</section>

<!-- Page: step 5 -->
<section class="page page--5">
  <header class="topbar">
    <div class="brand"><span class="brand__mark"></span><div><div class="brand__name">TALL PINE</div><div class="brand__tag">GROWTH MARKETING</div></div></div>
    <div class="callout">OR CALL US NOW : <b>(480) 555-0142</b></div>
    <a class="cta">GROW YOUR REVENUE</a>
  </header>
  <nav class="nav"><span>HOME</span><span>ABOUT</span><span>INDUSTRIES</span><span>SERVICES</span><span>RESOURCES</span><span>TRAINING</span><span>BLOG</span><span>CONTACT US</span></nav>
  <main class="main">
    <h1 class="title">GET A FREE ASSESSMENTS</h1>
    <div class="stepper"><span class="dot on">1</span><span class="link on"></span><span class="dot on">2</span><span class="link on"></span><span class="dot on">3</span><span class="link on"></span><span class="dot on">4</span><span class="link on"></span><span class="dot on">5</span></div>
    <div class="step">
      <div class="step__head">
        <svg class="step__icon" viewBox="0 0 26 26" fill="none" stroke="#7a1317" stroke-width="1.2"><rect x="5" y="2" width="17" height="22" rx="1"/><rect x="8" y="5" width="6" height="7"/><circle cx="11" cy="7.5" r="1.3"/><path d="M16 6h4M16 9h4M8 15h11M8 18h11M8 21h7M2 8h3M2 14h3M2 20h3"/></svg>
        <div><div class="step__num">Step 5</div><div class="step__q">What is your personal information</div></div>
      </div>
      <div class="grid5">
        <div class="field">Name</div><div class="field">Phone</div>
        <div class="field email">Email Address</div>
        <div class="submit">SUBMIT <span>›</span></div>
      </div>
    </div>
  </main>
  <div class="badges">
    <div class="brand"><span class="brand__mark"></span><div><div class="brand__name">TALL PINE</div><div class="brand__tag">GROWTH MARKETING</div></div></div>
    <div class="partner"><span class="partner__strip"></span><span class="partner__plate"></span></div>
    <span class="seal"></span>
    <div class="follow"><div class="follow__label">FOLLOW US</div><div class="socials"><span></span><span></span><span></span><span></span><span></span></div></div>
  </div>
  <div class="links">
    <ul class="col col--quick"><h3>QUICK LINKS</h3><li>About</li><li>Industries</li><li>Services</li><li>Resources</li><li>Training</li><li>Blog</li><li>Contact Us</li></ul>
    <ul class="col col--services"><h3>SERVICES</h3><li>Programmatic Advertising</li><li>Search Engine Marketing (SEM)</li><li>Search Engine Optimization (SEO)</li><li>Content Marketing</li><li>Email Marketing</li><li>Paid Search Advertising</li><li>Paid Social Advertising</li></ul>
    <ul class="col col--industries"><h3>INDUSTRIES</h3><li>Ecommerce</li><li>Electricians</li><li>Financial Services Marketing</li><li>Home Builders</li><li>Home Services</li><li>Hvac Companies</li><li>Cosmetic Surgery Centers</li><li>Dental Marketing</li></ul>
    <ul class="col col--guides"><h3>GUIDES</h3><li>Ultimate Guide On Growing Your Medical Practice Business</li><li>Legal Marketing Strategy Guide For Law Firm Offices</li><li>Ultimate Flashgram Ads Guide To Skyrocket Your Leads And Sales</li><li>Ultimate Guide To Search Engine Queries</li></ul>
  </div>
  <footer class="legal">Copyright © 2024 CompanyName&nbsp; All Rights Reserved. Privacy Policy, Terms Of Use, Press &amp; Media, Cookie Policy</footer>
</section>

</div>
</body>
</html>
```